Flyer Design Project

A beauty salon Velmira Spa needs a flyer design to promote some new services that are available in the salon. These are anti-aging, slimming and other treatments performed on the modern high-tech cosmetological equipment.
The flyer will be distrubuted in hi-end supermarket located near the salon. It would go inside the bags when the purchases are packed at the cashier desk.
The main idea is make people read it and not to throw it away immediately. The flyer will be printed on the top quality paper.
There will either be a discound or a promotional treatment in the flyer.
We are not sure about the size of the flyer. It should not be too big neither too small. Ideally on the one side there should be information about Facial Treatments and on the other about the Body Treatments. However we are open for other suggestions of the Pixel Forum.
This is our web-site www.velmira-spa.ru
Though being in Russian, it may give you an idea of our concept.
Updates

Thanks for all the designs submitted.

One general comment would be - the flyer should look different from the usual flyer one might get regarding the beauty salon services. Please make it attractive and unusual. Thanks.

Target Market(s)

Ladies from 25 to 60 years old who are well-to-do

Industry/Entity Type

Beauty Salon

Requirements
Nice to have
• It would be nice to have some technical features in the design.
Should not have
• The flyer should not be overloaded with pictures or graphic design features. It should be elegant and clear. The design should not look too "spa" as we promote technological treatments not massages.

```html
<!DOCTYPE html>
<html lang="ru">
<head>
<meta charset="utf-8">
<title>Velmira Spa — Body &amp; Facial Treatments Flyer</title>
<link rel="stylesheet" href="https://fonts.googleapis.com/css2?family=Didact+Gothic&family=Pinyon+Script&display=swap">
<style>
  :root {
    --canvas-bg: #e6e6e6;
    --brown-deep: #3a1a16;
    --brown-warm: #7b3b2c;
    --brown-dark: #4a2119;
    --black-wave: #120c0b;
    --accent-pink: #e0245a;
    --script-pink: #c43d63;
    --wood-light: #5a3a30;
    --wood-dark: #2e1b17;
    --paper: #ffffff;
    --text-light: #f3ece8;
    --text-dark: #1c1614;
  }
  * { margin: 0; padding: 0; box-sizing: border-box; }
  html, body { width: 1200px; height: 900px; overflow: hidden; }
  body {
    background: var(--canvas-bg);
    position: relative;
    font-family: "Didact Gothic", "Century Gothic", sans-serif;
  }
  .flyer {
    position: absolute;
    overflow: hidden;
    background: var(--paper);
  }
  .flyer--body { left: 30px; top: 80px; width: 582px; height: 755px; }
  .flyer--facial { left: 543px; top: 15px; width: 582px; height: 790px; }
  .flyer__shapes { position: absolute; inset: 0; width: 100%; height: 100%; }

  .brand {
    position: absolute;
    display: flex;
    align-items: center;
    gap: 18px;
    color: var(--paper);
  }
  .brand__dot {
    width: 30px; height: 30px; border-radius: 50%;
    background: var(--paper);
  }
  .brand__name {
    font-size: 50px;
    line-height: 1;
    letter-spacing: -0.5px;
  }
  .brand__tagline {
    font-size: 19px;
    line-height: 1.05;
    margin-left: 4px;
  }
  .flyer--body .brand { left: 86px; top: 58px; }
  .flyer--facial .brand { left: 82px; top: 78px; }

  .photo { position: absolute; }
  .photo--relax {
    left: 0; top: 228px; width: 392px; height: 222px;
    background: linear-gradient(100deg, #f3f1ee 0%, #e9d5c6 30%, #d8b49c 55%, #6b4a38 80%, #f5efe9 100%);
  }
  .photo--device {
    left: 226px; top: 262px; width: 346px; height: 212px;
    background: linear-gradient(90deg, #f4f6f7 0%, #dfe6ea 40%, #eadfd6 65%, #d6dde2 100%);
  }

  .section-title {
    position: absolute;
    font-family: "Pinyon Script", cursive;
    color: var(--script-pink);
    font-size: 36px;
    line-height: 1;
    white-space: nowrap;
    text-shadow: 1px 1px 0 rgba(0,0,0,0.35);
  }
  .flyer--body .section-title { left: 114px; top: 470px; }
  .flyer--facial .section-title { left: 230px; top: 490px; }

  .copy {
    position: absolute;
    font-size: 9.6px;
    line-height: 12px;
  }
  .copy--body {
    left: 92px; top: 510px; width: 296px;
    text-align: right; color: var(--text-light);
  }
  .copy--facial-left {
    left: 38px; top: 494px; width: 172px;
    text-align: justify; color: var(--text-dark);
  }
  .copy--facial-right {
    left: 230px; top: 526px; width: 290px;
    text-align: left; color: var(--text-light);
  }
</style>
</head>
<body>

<!-- Body treatments side -->
<section class="flyer flyer--body" aria-label="Body Treatments side">
  <svg class="flyer__shapes" viewBox="0 0 582 755" preserveAspectRatio="none" aria-hidden="true">
    <defs>
      <linearGradient id="woodBody" x1="0" y1="0" x2="1" y2="1">
        <stop offset="0" stop-color="var(--wood-light)"/>
        <stop offset="0.5" stop-color="#3f2722"/>
        <stop offset="1" stop-color="var(--wood-dark)"/>
      </linearGradient>
    </defs>
    <rect width="582" height="180" fill="var(--brown-deep)"/>
    <path d="M0 108 C160 150 360 80 582 118 L582 256 C470 258 390 226 300 222 C190 218 90 240 0 232 Z" fill="var(--black-wave)"/>
    <path d="M0 162 C70 205 150 228 230 222 C350 212 460 150 582 142 L582 156 C460 166 350 228 230 236 C150 242 70 220 0 178 Z" fill="var(--accent-pink)"/>
    <rect x="0" y="452" width="582" height="303" fill="url(#woodBody)"/>
    <path d="M0 452 L582 452 L582 470 L110 470 Z" fill="#24140f" opacity="0.5"/>
  </svg>

  <div class="brand">
    <span class="brand__dot"></span>
    <span class="brand__name">Velmira Spa</span>
    <span class="brand__tagline">салон<br>красоты</span>
  </div>

  <div class="photo photo--relax" role="img" aria-label="Photo: woman relaxing on a towel with a spa bowl, soap bars and vanilla flower"></div>

  <h2 class="section-title">Body Treatments</h2>
  <p class="copy copy--body">Lorem ipsum dolor sit amet, consectetuer adipiscing elit. Aenean commodo ligula eget dolor. Aenean massa. Cum sociis natoque penatibus et magnis dis parturient montes, nascetur ridiculus mus. Donec quam felis, ultricies nec, pellentesque eu, pretium quis, sem. Nulla consequat massa quis enim. Donec pede justo, fringilla vel, aliquet nec, vulputate eget, arcu. In enim justo, rhoncus ut, imperdiet a, venenatis vitae, justo. Nullam dictum felis eu pede mollis pretium. Integer tincidunt. Cras dapibus. Vivamus elementum semper nisi. Aenean vulputate eleifend tellus. Aenean leo ligula, porttitor eu, consequat vitae, eleifend ac, enim. Aliquam lorem ante, dapibus in, viverra quis, feugiat a, tellus. Phasellus viverra nulla ut metus varius laoreet. Quisque rutrum. Aenean imperdiet. Etiam ultricies nisi vel augue. Curabitur ullamcorper ultricies nisi. Nam eget dui. Etiam rhoncus. Maecenas tempus, tellus eget condimentum rhoncus, sem quam semper libero, sit amet adipiscing</p>
</section>

<!-- Facial treatments side -->
<section class="flyer flyer--facial" aria-label="Facial Treatments side">
  <svg class="flyer__shapes" viewBox="0 0 582 790" preserveAspectRatio="none" aria-hidden="true">
    <defs>
      <radialGradient id="topGlow" cx="0.25" cy="0.25" r="0.9">
        <stop offset="0" stop-color="#9a5444"/>
        <stop offset="0.6" stop-color="var(--brown-warm)"/>
        <stop offset="1" stop-color="var(--brown-dark)"/>
      </radialGradient>
      <linearGradient id="woodFacial" x1="0" y1="0" x2="1" y2="1">
        <stop offset="0" stop-color="var(--wood-light)"/>
        <stop offset="0.55" stop-color="#3c2520"/>
        <stop offset="1" stop-color="var(--wood-dark)"/>
      </linearGradient>
    </defs>
    <rect width="582" height="260" fill="var(--black-wave)"/>
    <path d="M60 0 L582 0 L582 150 C470 190 340 212 220 200 C150 192 100 160 80 120 C66 80 62 40 60 0 Z" fill="url(#topGlow)"/>
    <path d="M0 40 C10 90 30 150 70 200" stroke="var(--brown-warm)" stroke-width="3" fill="none"/>
    <path d="M18 0 C24 60 40 120 80 170" stroke="var(--brown-warm)" stroke-width="2" fill="none"/>
    <path d="M0 222 C120 232 250 200 360 188 C450 178 520 172 582 180 L582 196 C520 188 450 194 360 204 C250 216 120 246 0 240 Z" fill="var(--accent-pink)"/>
    <rect x="0" y="240" width="214" height="240" fill="url(#woodFacial)"/>
    <path d="M214 252 C330 250 460 228 582 212 L582 480 L214 480 Z" fill="var(--paper)"/>
    <rect x="214" y="480" width="368" height="310" fill="url(#woodFacial)"/>
    <path d="M582 590 C560 690 480 760 390 790 L420 790 C500 760 575 690 582 630 Z" fill="var(--paper)"/>
    <path d="M582 660 C560 720 520 760 470 790 L490 790 C535 765 570 725 582 690 Z" fill="var(--paper)"/>
  </svg>

  <div class="brand">
    <span class="brand__dot"></span>
    <span class="brand__name">Velmira Spa</span>
    <span class="brand__tagline">салон<br>красоты</span>
  </div>

  <div class="photo photo--device" role="img" aria-label="Photo: specialist performing a body treatment with modern cosmetology equipment"></div>

  <p class="copy copy--facial-left">Lorem ipsum dolor sit amet, consectetuer adipiscing elit. Aenean commodo ligula eget dolor. Aenean massa. Cum sociis natoque penatibus et magnis dis parturient montes, nascetur ridiculus mus. Donec quam felis, ultricies nec, pellentesque eu, pretium quis, sem. Nulla consequat massa quis enim. Donec pede justo, fringilla vel, aliquet nec, vulputate eget, arcu. In enim justo, rhoncus ut, imperdiet a, venenatis vitae, justo. Nullam dictum felis eu pede mollis pretium. Integer tincidunt. Cras dapibus. Vivamus elementum semper nisi. Aenean vulputate eleifend tellus. Aenean leo ligula, porttitor eu, consequat vitae, eleifend ac, enim. Aliquam lorem ante, dapibus in, viverra quis, feugiat a, tellus. Phasellus viverra nulla ut metus varius laoreet. Quisq</p>

  <h2 class="section-title">Facial Treatments</h2>
  <p class="copy copy--facial-right">Lorem ipsum dolor sit amet, consectetuer adipiscing elit. Aenean commodo ligula eget dolor. Aenean massa. Cum sociis natoque penatibus et magnis dis parturient montes, nascetur ridiculus mus. Donec quam felis, ultricies nec, pellentesque eu, pretium quis, sem. Nulla consequat massa quis enim. Donec pede justo, fringilla vel, aliquet nec, vulputate eget, arcu. In enim justo, rhoncus ut, imperdiet a, venenatis vitae, justo. Nullam dictum felis eu pede mollis pretium. Integer tincidunt. Cras dapibus. Vivamus elementum semper nisi. Aenean vulputate eleifend tellus. Aenean leo ligula, porttitor eu, consequat vitae, eleifend ac, enim. Aliquam lorem ante, dapibus in, viverra quis, feugiat a, tellus. Phasellus viverra nulla ut metus varius laoreet. Quisque rutrum. Aenean imperdiet. Etiam ultricies nisi vel augue. Curabitur ullamcorper ultricies nisi. Nam eget dui. Etiam rhoncus. Maecenas tempus, tellus eget condimentum rhoncus, sem quam semper libero, sit amet adipiscing sem neque sed ipsum. Nam quam nunc, blandit vel, luctus pulvinar, hendrerit id, lorem. Maecenas nec odio et ante tincidunt tempus.</p>
</section>

</body>
</html>
```